Inspirational Quotes Poster Set

Brookloft is a stylish coworking space, which has a design-oriented vintage look from the 60's with an industrial touch (www.brookloft-example.com) Brookloft Quote Poster Set of 16 posters. The poster should be typo oriented and rather simple. Reflecting a bit the clean billboard design from the sixties. Minimal / simple graphical elements

Target Market(s)

Startups and Entrepreneurs

Industry/Entity Type

Startup

Font styles to use
Sans Serif

Colors

Designer to choose colors to be used in the design.

Requirements
Must have
• Posters need to be on and very stylish

```html
<!DOCTYPE html>
<html lang="en">
<head>
<meta charset="utf-8">
<title>Brookloft Quote Poster Set – Never Give Up</title>
<link href="https://fonts.googleapis.com/css2?family=Bebas+Neue&family=Carlito:wght@700&display=swap" rel="stylesheet">
<style>
  :root {
    --poster-yellow: #F6CF3E;
    --poster-red: #F12B16;
  }
  html, body {
    margin: 0;
    padding: 0;
    overflow: hidden;
    background: var(--poster-yellow);
  }
  .poster {
    width: 738px;
    height: 1200px;
    position: relative;
    overflow: hidden;
    background: var(--poster-yellow);
  }
  .poster svg {
    position: absolute;
    inset: 0;
    display: block;
  }
  .headline {
    font-family: "Bebas Neue", "Oswald", sans-serif;
    fill: var(--poster-red);
  }
  .headline-never { font-size: 194px; }
  .headline-giveup { font-size: 242px; }
  .attribution {
    font-family: "Carlito", "Calibri", "Open Sans", sans-serif;
    font-weight: 700;
    font-size: 40px;
    fill: var(--poster-red);
  }
</style>
</head>
<body>
  <main class="poster">
    <svg width="738" height="1200" viewBox="0 0 738 1200" xmlns="http://www.w3.org/2000/svg">
      <defs>
        <linearGradient id="thumbFill" x1="0" y1="0" x2="1" y2="0">
          <stop offset="0" stop-color="#F12B16"/>
          <stop offset="1" stop-color="#F2431C"/>
        </linearGradient>
      </defs>

      <rect class="thumbs-up-area" x="0" y="154" width="274" height="336" rx="40"
            fill="url(#thumbFill)" role="img"
            aria-label="Thumbs-up hand illustration in red"/>

      <g class="headline headline-never">
        <text x="308" y="272" textLength="363" lengthAdjust="spacingAndGlyphs">NEVER</text>
        <text x="306" y="471" textLength="363" lengthAdjust="spacingAndGlyphs">NEVER</text>
        <text x="308" y="669" textLength="363" lengthAdjust="spacingAndGlyphs">NEVER</text>
      </g>

      <text class="headline headline-giveup" x="89" y="896" textLength="581" lengthAdjust="spacingAndGlyphs">GIVE UP.</text>

      <g class="attribution" text-anchor="middle">
        <text x="367" y="1074">Walter Ashcombe</text>
        <text x="367" y="1137">British Prime Minister</text>
      </g>
    </svg>
  </main>
</body>
</html>
```